Holiday Rental Company Flyer Design (DL not A5)

Note from Brandloom Administration: The category sizing selected is A5, however the project requires DL sized artwork. Please refer to the DL template link below while the 'Special Requirements' are updated accordingly.

Project Brief:
We need a double sided DL flyer designed for an up market Holiday Rental Company that portrays a personalised approach to property management. These are to be used for letter box drops to homes we're specifically targeting so the design should be modern, complimentary colour palette, uncluttered & visually appealing.

Please Download the DL Template from Quillora here: http://www.quillora.com.au/ql/ns/propath/UploadResources.aspx?selectedTab=0?pfid=KMT&pf_id=KMT&xnav=easypath-upload-image#Templates

Target Market(s)

Wealthy Home Owners

Industry/Entity Type

It Company

Other font styles liked:
• Avant Garde Extra Light & Demi

Colors
33b8a4

Requirements
Must have
• DL Flyer sizes (210mm width x 99mm width, plus 3mm bleed)
• Front: Logo, Main Image & Grab
• Back: Contact Details & Brief Description of our business
• Images: Ideally the main image should be the house with the pool but alternatively a lifestyle images could also be used.
Nice to have
• A creative designer!
Should not have
• Clutter & busy designs

```html
<!DOCTYPE html>
<html lang="en">
<head>
<meta charset="utf-8">
<title>Harbourline Stays – DL Flyer</title>
<link href="https://fonts.googleapis.com/css2?family=Oswald:wght@300;400;600&family=Raleway:wght@500&display=swap" rel="stylesheet">
<style>
  :root{
    --teal:#2fb39e;
    --charcoal:#3b3b3d;
    --white:#ffffff;
    --paper:#f3f5f5;
    --stage:#e6e7e8;
    --text-soft:#e9ecec;
  }
  *{margin:0;padding:0;box-sizing:border-box}
  html,body{width:1200px;height:1187px;overflow:hidden}
  body{background:var(--stage);position:relative;font-family:"Raleway",sans-serif}
  .flyer{position:absolute;top:58px;width:520px;height:1070px;background:var(--charcoal);overflow:hidden;box-shadow:0 6px 18px rgba(0,0,0,.25)}
  .flyer--front{left:60px}
  .flyer--back{left:620px}
  .flyer__art{position:absolute;inset:0;width:520px;height:1070px}

  .like-us{position:absolute;font-family:"Oswald",sans-serif;font-weight:400;font-size:17px;letter-spacing:.5px;color:var(--white);display:flex;align-items:center;gap:9px}
  .like-us__square{width:20px;height:20px;background:var(--white)}
  .like-us--front{top:52px;left:34px}
  .like-us--back{top:990px;right:26px;font-size:14px}
  .like-us--back .like-us__square{background:var(--teal);width:17px;height:17px}

  .brand{position:absolute;font-family:"Oswald",sans-serif;font-weight:400;font-size:25px;letter-spacing:0;text-align:center;color:var(--charcoal);white-space:nowrap}
  .brand--front{left:260px;top:630px;width:240px}
  .brand--back{left:250px;top:76px;width:240px}

  .phone-bar{position:absolute;left:28px;top:764px;display:flex;align-items:center;gap:12px;font-family:"Oswald",sans-serif;font-weight:400;font-size:31px;color:var(--charcoal)}
  .phone-bar svg{width:30px;height:30px}

  .tagline{position:absolute;left:30px;top:900px;font-family:"Oswald",sans-serif;text-transform:uppercase;line-height:1.08}
  .tagline__line{display:block}
  .tagline__line--light{font-weight:300;font-size:44px;color:var(--white)}
  .tagline__line--bold{font-weight:600;font-size:62px;color:var(--charcoal);letter-spacing:.5px}
  .tagline__line--soft{font-weight:300;font-size:44px;color:var(--charcoal)}

  .section-title{position:absolute;left:32px;top:200px;font-family:"Oswald",sans-serif;text-transform:uppercase;line-height:1.05}
  .section-title__kicker{display:block;font-weight:400;font-size:22px;color:var(--white)}
  .section-title__main{display:block;font-weight:600;font-size:36px;color:var(--teal)}

  .service-list{position:absolute;left:32px;top:292px;width:440px;list-style:none;font-size:15px;font-weight:500;line-height:1.45;color:var(--text-soft)}
  .service-list li{position:relative;padding-left:22px;margin-bottom:16px}
  .service-list li::before{content:"";position:absolute;left:2px;top:8px;width:8px;height:8px;border-radius:50%;background:var(--teal)}

  .benefit-list{position:absolute;left:34px;top:462px;width:228px;list-style:none;font-size:13px;font-weight:500;line-height:1.4;color:var(--text-soft)}
  .benefit-list li{display:flex;gap:9px;margin-bottom:11px}
  .benefit-list svg{flex:none;width:13px;height:13px;margin-top:3px}

  .contact{position:absolute;right:22px;top:600px;text-align:right;font-family:"Oswald",sans-serif;font-style:normal;color:var(--white)}
  .contact__title{font-weight:600;font-size:22px;color:var(--teal);margin-bottom:14px}
  .contact__line{display:flex;justify-content:flex-end;align-items:center;gap:8px;font-weight:400;font-size:15px;line-height:1.75}
  .contact__line svg{width:11px;height:11px}
</style>
</head>
<body>

<section class="flyer flyer--front" aria-label="Flyer front">
  <svg class="flyer__art" viewBox="0 0 520 1070">
    <defs>
      <linearGradient id="bay" x1="0" y1="0" x2="0" y2="1">
        <stop offset="0" stop-color="#cfe0ec"/>
        <stop offset=".42" stop-color="#9ec4dc"/>
        <stop offset=".46" stop-color="#5aa3c4"/>
        <stop offset="1" stop-color="#2e7fa4"/>
      </linearGradient>
      <linearGradient id="bedroom" x1="0" y1="0" x2="1" y2="1">
        <stop offset="0" stop-color="#e8d2b0"/>
        <stop offset="1" stop-color="#b88b5e"/>
      </linearGradient>
      <linearGradient id="bathroom" x1="0" y1="0" x2="1" y2="1">
        <stop offset="0" stop-color="#d8d6d0"/>
        <stop offset="1" stop-color="#8f8c86"/>
      </linearGradient>
    </defs>

    <path role="img" aria-label="Photo: wooden sailboat moored on a calm bay" d="M0,0 H520 V262 L235,532 Q180,580 120,540 L0,455 Z" fill="url(#bay)"/>
    <path d="M0,470 L118,552 Q184,598 245,542 L520,282" fill="none" stroke="var(--white)" stroke-width="10"/>
    <path d="M0,500 L118,582 Q190,630 262,562 L520,316" fill="none" stroke="var(--teal)" stroke-width="16"/>

    <polygon points="0,0 240,0 0,240" fill="var(--teal)"/>

    <g transform="translate(560,450) rotate(45)">
      <rect role="img" aria-label="Photo: bright bedroom interior" x="-84" y="-84" width="168" height="168" rx="22" fill="url(#bedroom)" stroke="var(--charcoal)" stroke-width="8"/>
    </g>

    <polygon points="0,880 430,880 520,970 520,1070 0,1070" fill="var(--teal)"/>

    <g transform="translate(548,850) rotate(45)">
      <rect role="img" aria-label="Photo: modern bathroom with freestanding bath" x="-68" y="-68" width="136" height="136" rx="18" fill="url(#bathroom)" stroke="var(--charcoal)" stroke-width="8"/>
    </g>

    <g transform="translate(380,646) rotate(45)">
      <rect x="-108" y="-108" width="216" height="216" rx="30" fill="var(--teal)" stroke="var(--charcoal)" stroke-width="8"/>
    </g>

    <polygon points="0,760 335,760 303,820 0,820" fill="var(--white)"/>
  </svg>

  <div class="like-us like-us--front"><span>LIKE US</span><span class="like-us__square"></span></div>

  <div class="brand brand--front">Harbourline Stays</div>

  <div class="phone-bar">
    <svg viewBox="0 0 24 24"><path fill="var(--teal)" d="M6.6 10.8a15 15 0 0 0 6.6 6.6l2.2-2.2a1 1 0 0 1 1-.25 11.4 11.4 0 0 0 3.6.6 1 1 0 0 1 1 1V20a1 1 0 0 1-1 1A17 17 0 0 1 3 4a1 1 0 0 1 1-1h3.5a1 1 0 0 1 1 1c0 1.25.2 2.45.6 3.6a1 1 0 0 1-.25 1z"/></svg>
    <span>(03)5012 4470</span>
  </div>

  <h1 class="tagline">
    <span class="tagline__line tagline__line--light">Holiday Rental</span>
    <span class="tagline__line tagline__line--bold">Management</span>
    <span class="tagline__line tagline__line--soft">With a Difference</span>
  </h1>
</section>

<section class="flyer flyer--back" aria-label="Flyer back">
  <svg class="flyer__art" viewBox="0 0 520 1070">
    <defs>
      <linearGradient id="pool" x1="0" y1="0" x2="1" y2="1">
        <stop offset="0" stop-color="#4a3f7a"/>
        <stop offset=".55" stop-color="#6a5a9a"/>
        <stop offset="1" stop-color="#2d7fb8"/>
      </linearGradient>
      <linearGradient id="lounge" x1="0" y1="0" x2="1" y2="1">
        <stop offset="0" stop-color="#d9c7a8"/>
        <stop offset="1" stop-color="#8a6a48"/>
      </linearGradient>
    </defs>

    <path d="M82,0 H520 V160 H320 Q268,160 236,128 Z" fill="var(--paper)"/>
    <path d="M60,0 L222,146 Q258,178 320,178 H520" fill="none" stroke="var(--white)" stroke-width="9"/>
    <path d="M28,0 L200,168 Q242,206 320,206 H520" fill="none" stroke="var(--teal)" stroke-width="22"/>

    <path d="M520,360 L140,740" stroke="var(--white)" stroke-width="8"/>
    <path d="M520,398 L170,748" stroke="var(--teal)" stroke-width="32"/>

    <g transform="translate(80,930) rotate(45)">
      <rect role="img" aria-label="Photo: modern house with lit pool at dusk" x="-185" y="-185" width="370" height="370" rx="40" fill="url(#pool)" stroke="var(--charcoal)" stroke-width="10"/>
    </g>

    <path d="M520,880 L330,1070" stroke="var(--white)" stroke-width="8"/>
    <polygon points="520,918 520,1070 368,1070" fill="var(--teal)"/>

    <g transform="translate(318,1095) rotate(45)">
      <rect role="img" aria-label="Photo: living room with candles and plants" x="-110" y="-110" width="220" height="220" rx="24" fill="url(#lounge)" stroke="var(--charcoal)" stroke-width="10"/>
    </g>
  </svg>

  <div class="brand brand--back">Harbourline Stays</div>

  <h2 class="section-title">
    <span class="section-title__kicker">What we do</span>
    <span class="section-title__main">Differently!</span>
  </h2>

  <ul class="service-list">
    <li>Rather than relying upon a key safe or a central pick-up destination, a ‘Harbourline Stays’ staff member will greet guests upon arrival.</li>
    <li>Our ‘Meet &amp; Greet’ service provides home owners with an increased level of Security and also allows us to:</li>
  </ul>

  <ul class="benefit-list">
    <li><svg viewBox="0 0 14 14"><polyline points="2,7 6,11 12,3" fill="none" stroke="var(--teal)" stroke-width="2.2"/></svg><span>Prepare the home for their arrival (lights, heaters, music etc.)</span></li>
    <li><svg viewBox="0 0 14 14"><polyline points="2,7 6,11 12,3" fill="none" stroke="var(--teal)" stroke-width="2.2"/></svg><span>Establish a rapport &amp; help facilitate future bookings</span></li>
    <li><svg viewBox="0 0 14 14"><polyline points="2,7 6,11 12,3" fill="none" stroke="var(--teal)" stroke-width="2.2"/></svg><span>Reiterate their responsibilities to ensure the return of their bond</span></li>
  </ul>

  <address class="contact">
    <div class="contact__title">CONTACT US</div>
    <div class="contact__line"><span>(03)5012 4470</span><svg viewBox="0 0 24 24"><path fill="var(--teal)" d="M6.6 10.8a15 15 0 0 0 6.6 6.6l2.2-2.2a1 1 0 0 1 1-.25 11.4 11.4 0 0 0 3.6.6 1 1 0 0 1 1 1V20a1 1 0 0 1-1 1A17 17 0 0 1 3 4a1 1 0 0 1 1-1h3.5a1 1 0 0 1 1 1c0 1.250.2 2.450.6 3.6a1 1 0 0 1-.25 1z"/></svg></div>
    <div class="contact__line"><span>stay@harbourlinestays.com.au</span><svg viewBox="0 0 12 12"><rect x="1" y="2.5" width="10" height="7" fill="none" stroke="var(--teal)" stroke-width="1.4"/><polyline points="1,3 6,7 11,3" fill="none" stroke="var(--teal)" stroke-width="1.2"/></svg></div>
    <div class="contact__line"><span>harbourlinestays.com.au</span><svg viewBox="0 0 12 12"><circle cx="6" cy="6" r="4.8" fill="none" stroke="var(--teal)" stroke-width="1.4"/><line x1="1.2" y1="6" x2="10.8" y2="6" stroke="var(--teal)" stroke-width="1"/></svg></div>
    <div class="contact__line"><span>PO Box 18, Tidewater Victoria 3990</span><svg viewBox="0 0 12 12"><path d="M6 11 C3 7.5 2 6 2 4.5 A4 4 0 0 1 10 4.5 C10 6 9 7.5 6 11Z" fill="var(--teal)"/><circle cx="6" cy="4.5" r="1.4" fill="var(--charcoal)"/></svg></div>
  </address>

  <div class="like-us like-us--back"><span>LIKE US</span><span class="like-us__square"></span></div>
</section>

</body>
</html>
```